BMR Going Cashless

Hello,
We are a medical office looking to get a flyer created to promote to our patients we will be going "Cashless." Our tagline will be "Cash-Less is Stress-Less"

"Starting in July, to offer you the fastest and most convenient service, we are transitioning to a cashless system. You can now enjoy faster checkout times and greater security with card and contactless payments. More info to come."

I've added two other flyers as sample designs we've used.

Please include logo, addresses, website, phone number

Files to include jpeg, png, pdf (under 5mb), Facebook and Instagram sizing.

Thank you,
Lowen

```html
<!DOCTYPE html>
<html lang="en">
<head>
<meta charset="utf-8">
<title>BMR Going Cashless – Social Sizes</title>
<link href="https://fonts.googleapis.com/css2?family=Poppins:wght@400;500;600;700&display=swap" rel="stylesheet">
<style>
  :root{
    --board:#b3b3b3;
    --label:#333333;
    --card:#232323;
    --card-hi:#2e2e2e;
    --teal:#2fd1a6;
    --orange:#f47b3a;
    --paper:#e4e4e6;
    --ink:#2b2b2b;
    --white:#ffffff;
    --pin:#e8262b;
    --rule:#555555;
  }
  *{margin:0;padding:0;box-sizing:border-box}
  html,body{width:1200px;height:2898px;overflow:hidden}
  body{background:var(--board);font-family:"Poppins",sans-serif;position:relative}
  .size-label{position:absolute;left:0;width:100%;text-align:center;font-weight:700;font-size:45px;color:var(--label);letter-spacing:.5px}
  .card{position:absolute;left:168px;width:863px;overflow:hidden;
    background:radial-gradient(ellipse at 50% 35%,var(--card-hi),var(--card) 70%);
    box-shadow:0 8px 20px rgba(0,0,0,.25)}
  .card--square{top:200px;height:863px}
  .card--story{top:1261px;height:1535px}
  .abs{position:absolute}
  .brand{display:flex;align-items:center;gap:18px}
  .brand__dot{border-radius:50%;background:var(--teal)}
  .brand__name{font-weight:700;color:var(--orange);letter-spacing:2px;line-height:1}
  .headline{font-weight:700;line-height:1;letter-spacing:-1px}
  .headline .teal{color:var(--teal);display:block}
  .headline .orange{color:var(--orange);display:block}
  .photo{border-radius:50%;
    background:radial-gradient(circle at 40% 35%,#6b4a30 0%,#3a2a1e 35%,#1c2420 65%,#1f5a48 85%,#0e3a2e 100%)}
  .photo-ring{border-radius:50%;border:5px solid #2f6f5f;box-shadow:0 0 0 3px rgba(244,123,58,.35)}
  .badge{color:var(--white);text-align:center;font-weight:500;line-height:1}
  .badge svg{position:absolute;inset:0;width:100%;height:100%}
  .badge__text{position:relative;display:flex;flex-direction:column;align-items:center;justify-content:center;height:100%}
  .badge__text b{font-weight:700}
  .body-copy{color:var(--white);font-weight:400}
  .enjoy{color:var(--white);font-weight:400;letter-spacing:2px}
  .feature{display:flex;align-items:center;color:var(--white);font-weight:400;line-height:1.1}
  .feature svg{flex:none}
  .torn{position:absolute;left:0}
  .contact-title{color:var(--ink);font-weight:400}
  .office{color:var(--ink);font-weight:400}
  .office__tag{display:inline-block;background:var(--orange);color:var(--white);font-weight:600;padding:0 7px;line-height:1.35}
  .divider{position:absolute;width:1px;background:#9a9a9a}
  .pin{position:absolute}
  .accent{color:var(--orange)}
</style>
</head>
<body>

<div class="size-label" style="top:95px">1080 X 1080</div>

<!-- Square post -->
<section class="card card--square">
  <div class="abs photo-ring" style="left:458px;top:-50px;width:536px;height:536px"></div>
  <div class="abs photo" role="img" aria-label="Hand tapping a phone on a card payment terminal with teal glow" style="left:472px;top:-36px;width:508px;height:508px"></div>

  <div class="abs brand" style="left:60px;top:62px">
    <span class="brand__dot" style="width:40px;height:40px"></span>
    <span class="brand__name" style="font-size:64px">BMR</span>
  </div>

  <h1 class="abs headline" style="left:50px;top:192px;font-size:64px">
    <span class="teal">CASH-LESS IS</span>
    <span class="orange" style="margin-top:-2px">STRESS-LESS</span>
  </h1>

  <div class="abs badge" style="left:50px;top:359px;width:130px;height:130px">
    <svg viewBox="0 0 100 100"><g fill="var(--orange)">
      <rect x="14" y="14" width="72" height="72"/><rect x="14" y="14" width="72" height="72" transform="rotate(15 50 50)"/>
      <rect x="14" y="14" width="72" height="72" transform="rotate(30 50 50)"/><rect x="14" y="14" width="72" height="72" transform="rotate(45 50 50)"/>
      <rect x="14" y="14" width="72" height="72" transform="rotate(60 50 50)"/><rect x="14" y="14" width="72" height="72" transform="rotate(75 50 50)"/></g></svg>
    <div class="badge__text" style="font-size:17px"><span>STARTING</span><span>IN</span><b style="font-size:28px;margin-top:2px">JULY</b></div>
  </div>

  <p class="abs body-copy" style="left:190px;top:374px;font-size:21px;line-height:24px;width:330px">to offer you the fastest and most convenient service, we are transitioning to a cashless system.</p>

  <div class="abs enjoy" style="left:65px;top:525px;font-size:19px">YOU CAN NOW ENJOY</div>
  <div class="abs" style="left:310px;top:538px;right:0;height:1px;background:var(--rule)"></div>

  <div class="abs feature" style="left:63px;top:568px;gap:22px;font-size:21px">
    <svg width="40" height="40" viewBox="0 0 40 40"><circle cx="20" cy="20" r="11" fill="var(--teal)"/><path d="M6 18a14 14 0 0 1 24-9M34 22a14 14 0 0 1-24 9" fill="none" stroke="var(--orange)" stroke-width="3"/><path d="M30 3v7h-7M10 37v-7h7" fill="none" stroke="var(--orange)" stroke-width="3"/></svg>
    <span>Faster checkout<br>times</span>
  </div>
  <div class="abs feature" style="left:332px;top:568px;gap:22px;font-size:21px">
    <svg width="40" height="40" viewBox="0 0 40 40"><path d="M20 3l14 6v10c0 9-6 15-14 18C12 34 6 28 6 19V9z" fill="var(--teal)" stroke="var(--orange)" stroke-width="2"/><rect x="14" y="19" width="12" height="9" rx="1" fill="var(--orange)"/><path d="M16 19v-3a4 4 0 0 1 8 0v3" fill="none" stroke="var(--orange)" stroke-width="2"/></svg>
    <span>Greater security<br>with card</span>
  </div>
  <div class="abs feature" style="left:592px;top:568px;gap:22px;font-size:21px">
    <svg width="46" height="46" viewBox="0 0 46 46"><circle cx="18" cy="18" r="16" fill="var(--teal)"/><path d="M13 12a8 8 0 0 1 0 12M17 9a12 12 0 0 1 0 18" fill="none" stroke="var(--white)" stroke-width="2.4"/><rect x="24" y="26" width="20" height="15" rx="3" fill="var(--orange)"/><rect x="24" y="30" width="20" height="3" fill="var(--white)"/></svg>
    <span>Contactless<br>payments</span>
  </div>

  <svg class="torn" style="top:630px" width="863" height="240" viewBox="0 0 863 240">
    <polygon fill="var(--paper)" stroke="var(--white)" stroke-width="3" points="0,50 40,42 60,48 90,38 120,45 150,32 175,42 200,30 230,46 260,38 285,50 300,42 330,35 350,20 370,15 400,6 420,12 440,2 470,10 500,20 520,30 545,42 560,50 575,58 590,52 610,42 640,35 665,42 690,30 720,25 750,18 780,20 810,10 835,18 863,6 863,240 0,240"/>
  </svg>

  <div class="abs contact-title" style="left:60px;top:710px;font-size:18px">CONTACT US TODAY</div>
  <div class="abs" style="left:60px;top:737px;display:flex;align-items:center;gap:6px;font-size:23px;color:var(--ink)">
    <svg width="18" height="18" viewBox="0 0 24 24"><path d="M6 2l4 4-2 3c1 3 4 6 7 7l3-2 4 4-3 4C10 22 2 14 2 5z" fill="var(--orange)"/></svg>(800)555-0142
  </div>
  <div class="abs" style="left:60px;top:770px;display:flex;align-items:center;gap:10px;font-size:18px;color:var(--ink)">
    <svg width="16" height="16" viewBox="0 0 24 24"><circle cx="12" cy="12" r="10" fill="none" stroke="var(--orange)" stroke-width="2"/><path d="M2 12h20M12 2c4 4 4 16 0 20M12 2c-4 4-4 16 0 20" fill="none" stroke="var(--orange)" stroke-width="2"/></svg>www.bmrcare.com
  </div>

  <div class="divider" style="left:457px;top:705px;height:124px"></div>
  <div class="divider" style="left:639px;top:705px;height:124px"></div>

  <svg class="pin" style="left:282px;top:705px" width="20" height="26" viewBox="0 0 20 26"><path d="M10 0a9 9 0 0 1 9 9c0 7-9 17-9 17S1 16 1 9a9 9 0 0 1 9-9z" fill="var(--pin)"/><circle cx="10" cy="9" r="3.5" fill="var(--white)"/></svg>
  <div class="abs office" style="left:286px;top:733px;font-size:14.5px;line-height:17px">
    <span class="office__tag" style="font-size:14px">Hillcrest Office</span><br>
    <span style="display:block;margin-top:4px">48 Maple Grove Rd.<br>Hillcrest, WV&nbsp; 25400</span>
  </div>

  <svg class="pin" style="left:515px;top:706px" width="20" height="26" viewBox="0 0 20 26"><path d="M10 0a9 9 0 0 1 9 9c0 7-9 17-9 17S1 16 1 9a9 9 0 0 1 9-9z" fill="var(--pin)"/><circle cx="10" cy="9" r="3.5" fill="var(--white)"/></svg>
  <div class="abs office" style="left:464px;top:734px;font-size:14.5px;line-height:17px">
    <span class="office__tag" style="font-size:14px">Brookfield Office</span><br>
    <span style="display:block;margin-top:6px">215 Oak Meadow Dr.<br>Ste. 120<br>Brookfield, MD 21700</span>
  </div>

  <svg class="pin" style="left:705px;top:706px" width="20" height="26" viewBox="0 0 20 26"><path d="M10 0a9 9 0 0 1 9 9c0 7-9 17-9 17S1 16 1 9a9 9 0 0 1 9-9z" fill="var(--pin)"/><circle cx="10" cy="9" r="3.5" fill="var(--white)"/></svg>
  <div class="abs office" style="left:647px;top:734px;font-size:14.5px;line-height:17px">
    <span class="office__tag" style="font-size:14px;padding-right:20px">Elmwood Office</span><br>
    <span style="display:block;margin-top:6px">2710 Riverside Blvd.<br>Ste. 305<br>Elmwood, MD 21705</span>
  </div>
</section>

<div class="size-label" style="top:1137px">1920 X 1080</div>

<!-- Story post -->
<section class="card card--story">
  <div class="abs brand" style="left:0;width:100%;top:80px;justify-content:center">
    <span class="brand__dot" style="width:46px;height:46px"></span>
    <span class="brand__name" style="font-size:76px">BMR</span>
  </div>

  <h1 class="abs headline" style="left:0;width:100%;top:208px;text-align:center;font-size:92px">
    <span class="teal">CASH-LESS IS</span>
    <span class="orange" style="margin-top:-4px">STRESS-LESS</span>
  </h1>

  <div class="abs photo-ring" style="left:142px;top:401px;width:580px;height:580px"></div>
  <div class="abs photo" role="img" aria-label="Hand tapping a phone on a card payment terminal with teal glow" style="left:168px;top:427px;width:528px;height:528px"></div>

  <div class="abs badge" style="left:118px;top:754px;width:232px;height:232px">
    <svg viewBox="0 0 100 100"><g fill="var(--orange)">
      <rect x="14" y="14" width="72" height="72"/><rect x="14" y="14" width="72" height="72" transform="rotate(15 50 50)"/>
      <rect x="14" y="14" width="72" height="72" transform="rotate(30 50 50)"/><rect x="14" y="14" width="72" height="72" transform="rotate(45 50 50)"/>
      <rect x="14" y="14" width="72" height="72" transform="rotate(60 50 50)"/><rect x="14" y="14" width="72" height="72" transform="rotate(75 50 50)"/></g></svg>
    <div class="badge__text" style="font-size:31px"><span>STARTING</span><span>IN</span><b style="font-size:52px;margin-top:2px">JULY</b></div>
  </div>

  <p class="abs body-copy" style="left:0;width:100%;top:996px;text-align:center;font-size:26px;line-height:30px;color:var(--teal);font-weight:500">to offer you the fastest and most convenient<br>service, we are transitioning to a cashless system.</p>

  <div class="abs enjoy" style="left:0;width:100%;top:1090px;text-align:center;font-size:21px;color:var(--orange);letter-spacing:3px">YOU CAN NOW ENJOY</div>

  <div class="abs feature" style="left:105px;top:1133px;gap:14px;font-size:22px">
    <svg width="40" height="40" viewBox="0 0 40 40"><circle cx="20" cy="20" r="11" fill="var(--teal)"/><path d="M6 18a14 14 0 0 1 24-9M34 22a14 14 0 0 1-24 9" fill="none" stroke="var(--orange)" stroke-width="3"/><path d="M30 3v7h-7M10 37v-7h7" fill="none" stroke="var(--orange)" stroke-width="3"/></svg>
    <span>Faster checkout<br>times</span>
  </div>
  <div class="abs feature" style="left:338px;top:1133px;gap:14px;font-size:22px">
    <svg width="40" height="40" viewBox="0 0 40 40"><path d="M20 3l14 6v10c0 9-6 15-14 18C12 34 6 28 6 19V9z" fill="var(--teal)" stroke="var(--orange)" stroke-width="2"/><rect x="14" y="19" width="12" height="9" rx="1" fill="var(--orange)"/><path d="M16 19v-3a4 4 0 0 1 8 0v3" fill="none" stroke="var(--orange)" stroke-width="2"/></svg>
    <span>Greater security<br>with card</span>
  </div>
  <div class="abs feature" style="left:576px;top:1131px;gap:16px;font-size:22px">
    <svg width="46" height="46" viewBox="0 0 46 46"><circle cx="18" cy="18" r="16" fill="var(--teal)"/><path d="M13 12a8 8 0 0 1 0 12M17 9a12 12 0 0 1 0 18" fill="none" stroke="var(--white)" stroke-width="2.4"/><rect x="24" y="26" width="20" height="15" rx="3" fill="var(--orange)"/><rect x="24" y="30" width="20" height="3" fill="var(--white)"/></svg>
    <span>Contactless<br>payments</span>
  </div>

  <svg class="torn" style="top:1224px" width="863" height="320" viewBox="0 0 863 320">
    <polygon fill="var(--paper)" stroke="var(--white)" stroke-width="3" points="0,52 30,46 55,50 80,40 110,44 140,34 170,40 200,28 225,32 250,18 275,22 300,10 330,14 360,4 390,8 420,20 450,32 475,42 500,56 520,62 540,58 565,46 590,40 620,44 650,36 680,30 710,34 740,22 770,24 800,16 830,10 863,2 863,320 0,320"/>
  </svg>

  <div class="divider" style="left:302px;top:1290px;height:103px"></div>
  <div class="divider" style="left:546px;top:1290px;height:103px"></div>

  <svg class="pin" style="left:74px;top:1300px" width="22" height="28" viewBox="0 0 20 26"><path d="M10 0a9 9 0 0 1 9 9c0 7-9 17-9 17S1 16 1 9a9 9 0 0 1 9-9z" fill="var(--pin)"/><circle cx="10" cy="9" r="3.5" fill="var(--white)"/></svg>
  <div class="abs office" style="left:106px;top:1302px;font-size:16.5px;line-height:19px">
    <span class="office__tag" style="font-size:16px">Hillcrest Office</span><br>
    <span style="display:block;margin-top:4px">48 Maple Grove Rd.<br>Hillcrest, WV&nbsp; 25400</span>
  </div>

  <svg class="pin" style="left:313px;top:1302px" width="22" height="28" viewBox="0 0 20 26"><path d="M10 0a9 9 0 0 1 9 9c0 7-9 17-9 17S1 16 1 9a9 9 0 0 1 9-9z" fill="var(--pin)"/><circle cx="10" cy="9" r="3.5" fill="var(--white)"/></svg>
  <div class="abs office" style="left:340px;top:1304px;font-size:16.5px;line-height:19px">
    <span class="office__tag" style="font-size:16px">Brookfield Office</span><br>
    <span style="display:block;margin-top:6px">215 Oak Meadow Dr.<br>Ste. 120<br>Brookfield, MD 21700</span>
  </div>

  <svg class="pin" style="left:561px;top:1302px" width="22" height="28" viewBox="0 0 20 26"><path d="M10 0a9 9 0 0 1 9 9c0 7-9 17-9 17S1 16 1 9a9 9 0 0 1 9-9z" fill="var(--pin)"/><circle cx="10" cy="9" r="3.5" fill="var(--white)"/></svg>
  <div class="abs office" style="left:590px;top:1304px;font-size:16.5px;line-height:19px">
    <span class="office__tag" style="font-size:16px;padding-right:22px">Elmwood Office</span><br>
    <span style="display:block;margin-top:6px">2710 Riverside Blvd.<br>Ste. 305<br>Elmwood, MD 21705</span>
  </div>

  <div class="abs" style="left:0;width:100%;top:1408px;display:flex;justify-content:center;align-items:center;gap:12px;color:var(--ink)">
    <span class="contact-title" style="font-size:26px">CONTACT US TODAY</span>
    <svg width="26" height="26" viewBox="0 0 24 24"><path d="M6 2l4 4-2 3c1 3 4 6 7 7l3-2 4 4-3 4C10 22 2 14 2 5z" fill="var(--orange)"/></svg>
    <span style="font-size:34px">(800)555-0142</span>
  </div>
  <div class="abs" style="left:0;width:100%;top:1450px;text-align:center;font-size:30px;color:var(--ink)">www.<span class="accent" style="font-weight:600">bmrcare</span>.com</div>
</section>

</body>
</html>
```